Restoration Large Account Loss Booklet

We need a booklet style brochure to look very similar to the uploaded presentation for a leave behind during presentations or handout for tradeshows. We specialize in COMMERCIAL ONLY disaster recovery services after major events like water and flood, fire and smoke, mold and biohazard and structural damage.

Target Market(s)

Real Estate, Commercial Facilities, Education Facilities, Hospitality Facilities

Industry/Entity Type

Construction

Colors
f78f20
3176b5
0355a3
ffffff

Requirements
Must have
• Pictures of commercial facilities, educational facilities, medical facilities, hospitality facilities. The coverage map from presentation, the information from The Amber Ladder (more of a "Who We Are"), some of the pictures from our case studies (do not put specific names), our provided services (water and flood, fire and smoke, mold and biohazard, structural repair, asset protection). Our motto. Specialization of industries. Our logo.
Nice to have
• Pictures of our equipment.
Should not have
• Do not put any specific names (Marlowe ISD, Birch St., etc). Do not put anything that looks even remotely close to residential pictures. Only commercial.

```html
<!DOCTYPE html>
<html lang="en">
<head>
<meta charset="utf-8">
<title>Ridgeway Restoration — Booklet</title>
<link href="https://fonts.googleapis.com/css2?family=Tinos:wght@400;700&family=Montserrat:wght@400;500;600&family=Open+Sans:ital,wght@0,400;1,600&display=swap" rel="stylesheet">
<style>
  :root{
    --orange:#ef7f1a;
    --orange-soft:rgba(239,127,26,.86);
    --teal:#2d5a6b;
    --ink:#4a4f55;
    --paper:#ffffff;
    --backdrop:#e4e4e4;
    --photo-dark:#3b3e42;
    --photo-mid:#7d8186;
  }
  *{box-sizing:border-box;margin:0;padding:0}
  html,body{width:1200px;height:900px;overflow:hidden}
  body{background:var(--backdrop);position:relative;font-family:"Montserrat",sans-serif}

  .page{position:absolute;width:520px;height:340px;background:var(--paper);overflow:hidden;box-shadow:0 6px 18px rgba(0,0,0,.12)}

  /* Cover */
  .cover{left:340px;top:60px}
  .cover-photo{position:absolute;left:14px;top:14px;right:14px;bottom:14px;
    background:linear-gradient(180deg,#5d6166 0%,#8a8d91 38%,var(--photo-dark) 62%,#24272a 100%)}
  .cover-frame{position:absolute;left:30px;top:30px;right:30px;bottom:30px;border:1.5px solid var(--orange)}
  .cover-band{position:absolute;left:128px;top:96px;right:0;height:118px;background:var(--orange-soft);padding:22px 0 0 26px;color:#fff}
  .cover-title{font-family:"Tinos",serif;font-weight:700;font-size:36px;line-height:36px;letter-spacing:1px}
  .cover-tagline{font-family:"Open Sans",sans-serif;font-style:italic;font-weight:600;font-size:10.5px;margin-top:6px}
  .cover-date{position:absolute;left:0;right:0;bottom:42px;text-align:center;color:#fff;font-family:"Open Sans",sans-serif;font-size:8px;letter-spacing:.5px}
  .cover-ticks{display:flex;justify-content:center;gap:4px;margin-bottom:4px}
  .cover-ticks span{width:18px;height:2px;background:#fff}
  .cover-ticks span:nth-child(2){background:#6a9bb0}
  .cover-ticks span:nth-child(3){background:var(--orange)}

  /* Inside spread */
  .spread-left{left:80px;top:470px;box-shadow:-4px 6px 18px rgba(0,0,0,.12)}
  .spread-right{left:600px;top:470px;box-shadow:4px 6px 18px rgba(0,0,0,.12)}
  .spread-fold{position:absolute;left:588px;top:470px;width:24px;height:340px;
    background:linear-gradient(90deg,rgba(0,0,0,0),rgba(0,0,0,.08),rgba(0,0,0,0))}

  .frame-line{position:absolute;inset:0}
  .motto-block{position:absolute;left:0;top:52px;width:140px;height:62px;background:var(--orange)}
  .motto-photo{position:absolute;left:92px;top:72px;width:228px;height:190px;
    background:linear-gradient(135deg,#c9ccd0 0%,#8f949a 45%,#4b4f55 100%)}
  .motto-accent{position:absolute;left:306px;top:112px;width:30px;height:30px;background:var(--orange)}
  .motto-text{position:absolute;left:340px;top:160px;width:160px}
  .motto-heading{color:var(--teal);font-weight:600;font-size:17px;letter-spacing:1px;margin-bottom:8px}
  .motto-body{color:var(--ink);font-size:9.5px;line-height:1.45}

  .brand{position:absolute;left:46px;top:42px;color:var(--orange);font-family:"Montserrat",sans-serif;font-weight:600;font-size:15px;line-height:1.2;letter-spacing:.5px;display:flex;align-items:center;gap:8px}
  .brand-mark{width:12px;height:12px;background:var(--orange);flex:none}
  .contents{position:absolute;left:268px;top:196px;list-style:none}
  .contents li{display:flex;align-items:baseline;gap:8px;margin-bottom:4px;color:var(--teal);font-size:8.5px;letter-spacing:.4px;text-transform:uppercase}
  .contents .num{font-size:15px;font-weight:500;border-left:1.5px solid var(--orange);padding-left:5px;width:34px}
</style>
</head>
<body>

<section class="page cover">
  <div class="cover-photo" role="img" aria-label="Grayscale photo of commercial buildings beside floodwater under cloudy sky"></div>
  <div class="cover-frame"></div>
  <div class="cover-band">
    <h1 class="cover-title">RIDGEWAY<br>RESTORATION</h1>
    <p class="cover-tagline">Exceeding your expectations when you need it most.</p>
  </div>
  <div class="cover-date">
    <div class="cover-ticks"><span></span><span></span><span></span></div>
    02.22.2018
  </div>
</section>

<section class="page spread-left">
  <svg class="frame-line" width="520" height="340" viewBox="0 0 520 340" aria-hidden="true">
    <path d="M60 40 H470 M60 40 V300 H470 M470 300 V200 M470 150 V40" fill="none" stroke="#ef7f1a" stroke-width="1.5" stroke-dasharray="none"/>
  </svg>
  <div class="motto-block"></div>
  <div class="motto-photo" role="img" aria-label="Photo of two business people shaking hands outside an office building"></div>
  <div class="motto-accent"></div>
  <div class="motto-text">
    <h2 class="motto-heading">COMPANY MOTTO</h2>
    <p class="motto-body">Ridgeway Restoration's goal is to create optimal VALUE through our efforts, efficiencies, quality of work and communication.</p>
  </div>
</section>

<div class="spread-fold"></div>

<section class="page spread-right">
  <svg class="frame-line" width="520" height="340" viewBox="0 0 520 340" aria-hidden="true">
    <path d="M40 290 H470 V230" fill="none" stroke="#ef7f1a" stroke-width="1.5"/>
  </svg>
  <div class="brand"><span class="brand-mark"></span><span>RIDGEWAY<br>RESTORATION SERVICES</span></div>
  <ol class="contents">
    <li><span class="num">01</span>Who we are and how we're different</li>
    <li><span class="num">02</span>Who and how we serve</li>
    <li><span class="num">03</span>Where we serve and why</li>
    <li><span class="num">04</span>Case studies</li>
  </ol>
</section>

</body>
</html>
```